Pyschiatry Experts need Marketing Campaign

Ad(s) developed for print advertising sharing our purpose and services, highlighting our medical care providers. Must be welcoming and inviting while displaying a high level of professionalism expected from a physician's office.

Target Market(s)

Local community

Industry/Entity Type

Psychiatry (Healthcare)

Requirements
Must have
• Staff pictures, 'Medication Management Experts', 'Prompt Appointments', 'ADD/ADHD, Bipolar Disorder, Depression, Anxiety, Schizophrenia, Grief Reaction and others' 'Virtual and In-Person Visits'
Nice to have
• Address: 412 E Marlowe Coeur d'Alene Phone (208)555-7193 website: BrightLoftCare.com Hours: Mon - Thur 7am - 6pm

```html
<!DOCTYPE html>
<html lang="en">
<head>
<meta charset="utf-8">
<title>Brightloft Health – Print Ad</title>
<link rel="stylesheet" href="https://fonts.googleapis.com/css2?family=Fira+Sans+Extra+Condensed:wght@400;600;700&family=Montserrat:wght@400;500;600;700&display=swap">
<style>
  :root{
    --backdrop:#3e6a70;
    --paper:#ffffff;
    --teal:#14a89a;
    --teal-deep:#17968a;
    --forest:#22513f;
    --lime:#acd558;
    --lime-text:#b5df5e;
    --sky:#e4f2f8;
    --ink:#1d1d1d;
    --ink-green:#2a4d3c;
  }
  *{box-sizing:border-box;margin:0;padding:0}
  html,body{width:1200px;height:1200px;overflow:hidden}
  body{background:var(--backdrop);position:relative;font-family:"Montserrat",sans-serif;color:var(--ink)}

  .flyer{position:absolute;left:233px;top:125px;width:734px;height:950px;background:var(--paper);overflow:hidden}

  .hero-photo{position:absolute;right:0;top:0;width:460px;height:425px;
    background:linear-gradient(90deg,#ffffff 0%,#f3f1ec 30%,#e6dfd3 65%,#d8cfc1 100%);}

  .brand{position:absolute;left:71px;top:44px;width:210px;text-align:center;color:var(--teal)}
  .brand-mark{width:60px;height:60px;border-radius:50%;background:var(--teal);margin:0 auto 12px}
  .brand-name{font-weight:600;font-size:24px;letter-spacing:1px;line-height:1}
  .brand-sub{font-weight:600;font-size:15px;letter-spacing:3px;margin-top:4px;line-height:1}

  .headline{position:absolute;left:54px;top:200px;font-family:"Fira Sans Extra Condensed",sans-serif;font-weight:700;font-size:42px;line-height:49px}
  .headline .lead{color:var(--teal)}
  .headline .key{color:var(--forest)}

  .services{position:absolute;left:54px;top:365px;font-family:"Fira Sans Extra Condensed",sans-serif;font-weight:400;font-size:18px;line-height:23px;color:var(--ink-green)}

  .providers-band{position:absolute;left:0;top:425px;width:734px;height:160px;background:var(--forest)}
  .lower-field{position:absolute;left:0;top:585px;width:734px;height:288px;background:linear-gradient(180deg,#f4fafc 0%,var(--sky) 100%)}

  .providers-title{position:absolute;left:0;top:433px;width:734px;text-align:center;font-family:"Fira Sans Extra Condensed",sans-serif;font-weight:700;font-size:31px;color:var(--lime-text)}
  .providers-intro{position:absolute;left:60px;top:474px;width:614px;text-align:center;font-size:11.2px;line-height:14.4px;color:#fff}

  .provider{position:absolute;top:532px;width:152px;height:152px;margin-left:-76px;border-radius:50%;background:#fff}
  .provider-card{position:absolute;top:542px;width:132px;height:203px;margin-left:-66px;border-radius:66px;background:var(--lime);text-align:center}
  .provider-photo{position:absolute;left:8px;top:8px;width:116px;height:116px;border-radius:50%;
    border:4px solid var(--teal-deep);border-top-color:var(--lime);border-right-color:var(--lime);
    transform:rotate(-45deg)}
  .provider-photo span{position:absolute;inset:0;border-radius:50%;background:linear-gradient(180deg,#6f7b81 0%,#4a555b 100%)}
  .provider-name{position:absolute;left:0;right:0;top:137px;font-weight:600;font-size:14.5px;color:var(--forest)}
  .provider-cred{position:absolute;left:0;right:0;top:156px;font-size:11.5px;color:var(--forest);letter-spacing:.3px}

  .migraine-copy{position:absolute;left:60px;top:760px;width:614px;text-align:center;font-size:11.6px;line-height:14.5px;color:var(--ink);white-space:nowrap}

  .rule{position:absolute;left:37px;top:829px;width:470px;height:1px;background:var(--teal-deep)}
  .offerings{position:absolute;left:33px;top:845px;font-size:11.2px;color:var(--ink);white-space:nowrap}
  .offerings span::before{content:"";display:inline-block;width:6px;height:6px;border-radius:50%;background:#111;margin:0 3px 1px 4px}

  .hours{position:absolute;left:520px;top:823px;width:214px;height:40px;background:var(--forest);border-radius:20px 0 0 20px;
    font-family:"Fira Sans Extra Condensed",sans-serif;font-weight:600;font-size:16.5px;color:#fff;line-height:40px;padding-left:21px}

  .contact-bar{position:absolute;left:0;top:873px;width:734px;height:77px;background:var(--lime)}
  .divider{position:absolute;top:7px;width:1px;height:62px;background:var(--teal-deep)}
  .contact-address{position:absolute;left:53px;top:22px;font-size:12px;line-height:15px;color:var(--ink)}
  .contact-address strong{font-weight:600}
  .contact-phone{position:absolute;left:317px;top:24px;font-weight:700;font-size:21px;color:#111}
  .contact-web{position:absolute;left:586px;top:30px;font-size:12.5px;color:#111}
  .icon{position:absolute}
</style>
</head>
<body>
<div class="flyer">
  <div class="hero-photo" role="img" aria-label="Photo of a smiling woman working on a laptop on a sofa in a bright living room"></div>

  <div class="brand">
    <div class="brand-mark"></div>
    <div class="brand-name">BRIGHTLOFT</div>
    <div class="brand-sub">HEALTH</div>
  </div>

  <h1 class="headline">
    <span class="lead">Helping</span> <span class="key">Bodies</span><br>
    <span class="lead">Helping</span> <span class="key">Minds</span><br>
    <span class="lead">Helping</span> <span class="key">You</span>
  </h1>

  <p class="services">Mental Health and Psychiatry Services<br>Migraine and Neurospasticity Intervention</p>

  <div class="providers-band"></div>
  <div class="lower-field"></div>

  <h2 class="providers-title">Meet Our Mental Health Providers</h2>
  <p class="providers-intro">Bringing comprehensive evaluation, medication management and psychotherapy to<br>the full spectrum of mental health disorders including minor, moderate and major depression,<br>bipolar disorder, ADD/ADHD, anxiety, schizophrenia, stress or grief reactions, and others.</p>

  <div class="provider" style="left:158px"></div>
  <div class="provider" style="left:303px"></div>
  <div class="provider" style="left:448px"></div>
  <div class="provider" style="left:593px"></div>

  <div class="provider-card" style="left:158px">
    <div class="provider-photo"><span role="img" aria-label="Headshot of provider Dan Whitcomb"></span></div>
    <div class="provider-name">Dan Whitcomb</div>
    <div class="provider-cred">PMHNP - BC</div>
  </div>
  <div class="provider-card" style="left:303px">
    <div class="provider-photo"><span role="img" aria-label="Headshot of provider Marla Ostrand"></span></div>
    <div class="provider-name">Marla Ostrand</div>
    <div class="provider-cred">PMHNP - BC</div>
  </div>
  <div class="provider-card" style="left:448px">
    <div class="provider-photo"><span role="img" aria-label="Headshot of provider Kent Barlow"></span></div>
    <div class="provider-name">Kent Barlow</div>
    <div class="provider-cred">PMHNP - BC</div>
  </div>
  <div class="provider-card" style="left:593px">
    <div class="provider-photo"><span role="img" aria-label="Headshot of provider Ruth Ellery"></span></div>
    <div class="provider-name">Ruth Ellery</div>
    <div class="provider-cred">PMHNP-BC, DNP</div>
  </div>

  <p class="migraine-copy">Migraine management and intervention can be a complex journey.&nbsp; Identifying food and<br>environmental triggers, identification of migraine type, pharmacological management with<br>a new generation of highly effective medications and/or botulinum injections are all part of<br>our comprehensive care program for migraine sufferers.</p>

  <div class="rule"></div>
  <p class="offerings"><span>New Patient Evaluation</span> <span>Insurance Pre-Authorization</span> <span>Follow-Up Appointments</span></p>

  <div class="hours">Hours: Mon - Thur 7am - 6pm</div>

  <div class="contact-bar">
    <svg class="icon" style="left:24px;top:24px" width="18" height="26" viewBox="0 0 18 26">
      <path d="M9 0C4 0 0 4 0 9c0 6.5 9 17 9 17s9-10.5 9-17C18 4 14 0 9 0z" fill="#17968a"/>
      <circle cx="9" cy="9" r="3.6" fill="#acd558"/>
    </svg>
    <p class="contact-address"><strong>Brightloft Health</strong><br>412 E Marlowe Coeur d'Alene</p>
    <div class="divider" style="left:254px"></div>

    <svg class="icon" style="left:282px;top:26px" width="25" height="25" viewBox="0 0 25 25">
      <circle cx="12.5" cy="12.5" r="12.5" fill="#17968a"/>
      <path d="M8.6 6.2c.6-.4 1.3-.2 1.6.4l1.2 2.3c.3.6.1 1.2-.4 1.6l-.8.6c.6 1.6 1.9 3 3.5 3.8l.7-.8c.4-.5 1.1-.6 1.6-.3l2.2 1.3c.6.3.8 1.1.4 1.6l-.9 1.2c-.6.8-1.7 1.1-2.7.7-3.5-1.4-6.2-4.200-7.4-7.8-.3-1 0-2 .8-2.6z" fill="#acd558"/>
    </svg>
    <p class="contact-phone">(208)555-7193</p>
    <div class="divider" style="left:512px"></div>

    <svg class="icon" style="left:550px;top:26px" width="25" height="25" viewBox="0 0 25 25" fill="none" stroke="#17968a" stroke-width="2">
      <circle cx="12.5" cy="12.5" r="11"/>
      <ellipse cx="12.5" cy="12.5" rx="5" ry="11"/>
      <path d="M2 9h21M2 16h21"/>
    </svg>
    <p class="contact-web">BrightLoftCare.com</p>
  </div>
</div>
</body>
</html>
```